Website for Briar Hollow Gathering Church

Wordpress website design required for Briar Hollow Gathering Church. We are a family oriented church catering for age groups from school age to elderly people. The church has a wide variety of activities which it coordinates. The idea is to describe the activities on the activities page, but cross-link them to show which would be applicable to the different age groups.

We would like an inviting website which is easy to read and navigate.

Target Market(s)

Very wide audience - from school age youth to elderly people, so design and style should cater for both audiences.

Industry/Entity Type

Church

Coding

Coded - Design and coding required

Number of Pages Required

5+ page

Font styles to use
Sans Serif

Colors
0255a3
ffffff
0792cd
f78f20

Requirements
Must have
• Inviting website.
• Clear readable font.
• Space to import photos to balance text on each page.
• Need to project a dynamic and progressive feel for the church.
• Easy to navigate.
Nice to have
• Scrolling photos on pages. Ability to enter questions/ comments/prayer requests on Home page.
Should not have
• Conservative audience, so should not be too bold.

```html
<!DOCTYPE html>
<html lang="en">
<head>
<meta charset="utf-8">
<title>Briar Hollow Gathering Church</title>
<link href="https://fonts.googleapis.com/css2?family=Crimson+Pro:wght@300;400&family=Open+Sans:wght@400;600&family=Raleway:wght@500;600&display=swap" rel="stylesheet">
<style>
:root{
  --blue-deep:#0255a3;
  --blue-nav:#0a5fae;
  --blue-dark:#064a90;
  --blue-sky:#0792cd;
  --blue-msg:#1698d4;
  --orange:#f78f20;
  --white:#ffffff;
  --grey-band:#e8e8e8;
  --text:#555a60;
  --text-soft:#8a8f95;
  --heading:#2b2f33;
}
*{margin:0;padding:0;box-sizing:border-box}
html,body{width:1200px;height:2839px;overflow:hidden}
body{font-family:"Open Sans",sans-serif;color:var(--text);background:var(--white);position:relative}
section,header,nav,footer{position:absolute;left:0;width:1200px}
h1,h2,h3,h4,h5{font-weight:400}

/* header */
.site-header{top:0;height:148px}
.brand{position:absolute;left:108px;top:86px;display:flex;align-items:center;gap:10px}
.brand-dot{width:16px;height:16px;border-radius:50%;background:var(--blue-deep)}
.brand-name{font-family:"Crimson Pro",serif;font-size:25px;font-weight:400;color:var(--blue-deep)}
.header-contact{position:absolute;right:124px;top:74px;text-align:right}
.header-contact small{display:block;font-size:17px;color:#a8adb2}
.header-contact strong{display:flex;align-items:center;gap:8px;font-size:27px;font-weight:400;color:var(--heading)}

/* nav */
.main-nav{top:148px;height:60px;background:linear-gradient(var(--blue-nav),var(--blue-deep))}
.main-nav ul{list-style:none;display:flex;margin-left:104px;height:60px}
.main-nav li{font-family:"Crimson Pro",serif;font-size:18px;color:var(--white);padding:0 29px;line-height:60px;border-right:1px solid rgba(255,255,255,.25)}
.main-nav li.active{background:var(--blue-dark)}
.main-nav li:last-child{border-right:none}

/* hero */
.hero{top:208px;height:470px}
.hero-photo{position:absolute;inset:0;background:radial-gradient(circle at 45% 55%,#8a6a2c 0,#4a3414 35%,#1e150b 80%)}
.hero-title{position:absolute;left:104px;top:170px;font-family:"Crimson Pro",serif;font-weight:400;font-size:38px;line-height:46px;color:var(--white);letter-spacing:.5px}
.hero-dots{position:absolute;left:553px;top:428px;display:flex;gap:5px}
.hero-dots span{width:18px;height:18px;border-radius:50%;background:var(--white)}
.hero-dots span.on{background:transparent;border:3px solid var(--white)}
.email-form{position:absolute;left:786px;top:82px;width:306px;height:287px;background:var(--blue-sky);padding:24px 28px}
.email-form h2{font-family:"Crimson Pro",serif;font-weight:400;font-size:27px;line-height:32px;color:var(--white)}
.email-form p{font-size:12px;color:#bfe4f5;margin:6px 0 14px}
.email-form .field{height:33px;background:var(--white);font-size:12px;color:#9aa;padding:9px 12px;margin-bottom:9px}
.email-form .submit{height:44px;background:#0d0d0d;color:var(--white);font-family:"Crimson Pro",serif;font-size:19px;text-align:center;line-height:44px;margin-top:10px}

/* welcome */
.welcome{top:678px;height:348px;text-align:center}
.welcome .kicker{display:flex;justify-content:center;align-items:center;gap:18px;margin-top:42px;font-family:"Crimson Pro",serif;font-size:33px;color:var(--blue-sky)}
.welcome .kicker i{display:block;width:150px;height:1px;background:#c9ccd0}
.welcome h1{font-family:"Crimson Pro",serif;font-size:33px;color:var(--heading)}
.welcome p{width:900px;margin:14px auto 0;font-size:15px;line-height:32px;color:var(--text)}
.btn-orange{display:inline-block;margin-top:24px;width:242px;height:50px;line-height:50px;background:var(--orange);color:var(--white);font-family:"Raleway",sans-serif;font-weight:600;font-size:18px}

/* activities */
.activities{top:1026px;height:354px;background:var(--grey-band)}
.section-title{font-family:"Crimson Pro",serif;font-weight:400;font-size:30px;color:var(--blue-deep);text-align:center}
.activities .section-title{margin-top:38px}
.activity-cards{position:absolute;left:104px;top:85px;display:flex;gap:12px}
.activity-card{width:240px}
.activity-card .photo{height:169px}
.activity-card .label{height:51px;background:var(--blue-deep);color:var(--white);font-family:"Raleway",sans-serif;font-weight:500;font-size:17px;text-align:center;line-height:51px}

/* minister */
.minister{top:1380px;height:337px;background:var(--blue-msg);text-align:center;color:var(--white)}
.minister h2{font-family:"Crimson Pro",serif;font-size:30px;margin-top:66px}
.minister p{width:790px;margin:12px auto 0;font-size:16px;line-height:30px}
.btn-outline{display:inline-block;border:2px solid var(--white);color:var(--white);font-family:"Raleway",sans-serif;font-weight:600;font-size:15px;height:42px;line-height:38px}
.minister .btn-outline{margin-top:24px;width:154px}

/* feature panels */
.panels{top:1742px;height:304px}
.panel{position:absolute;top:0;height:304px;text-align:center;color:var(--white)}
.panel.prayer{left:104px;width:496px;background:linear-gradient(135deg,#4a4a4a,#252525 60%,#3a3a3a)}
.panel.mission{left:604px;width:496px;background:linear-gradient(135deg,#f79a2c,#f07a10 55%,#f59530)}
.panel h3{font-family:"Crimson Pro",serif;font-size:31px;margin-top:60px}
.panel.mission h3{margin-top:72px}
.panel .sub{font-family:"Crimson Pro",serif;font-size:15px;margin-top:2px;letter-spacing:.5px}
.panel p{width:370px;margin:10px auto 0;font-size:13px;line-height:21px}
.prayer-form{display:flex;justify-content:center;margin-top:22px}
.prayer-form .field{width:257px;height:36px;background:var(--white);color:#a0a4a8;font-size:12px;text-align:left;padding:10px 12px}
.prayer-form .submit{width:108px;height:36px;background:var(--orange);font-family:"Raleway",sans-serif;font-weight:600;font-size:15px;line-height:36px}
.panel.mission .btn-outline{margin-top:18px;width:164px;height:38px;line-height:34px;font-size:14px}

/* news */
.news{top:2046px;height:447px}
.news .section-title{position:absolute;left:110px;top:38px;font-size:33px;color:var(--blue-sky)}
.news-list{position:absolute;left:108px;top:95px;display:flex;gap:15px}
.news-item{width:320px}
.news-item .photo{height:172px}
.news-item h4{font-family:"Raleway",sans-serif;font-weight:500;font-size:19px;color:var(--blue-deep);margin-top:22px}
.news-item p{font-size:13px;line-height:21px;color:var(--text-soft);margin-top:4px}
.news-item a{display:block;font-family:"Raleway",sans-serif;font-weight:600;font-size:13px;color:var(--orange);text-decoration:none;margin-top:6px}

/* footer */
.site-footer{top:2493px;height:293px;background:var(--blue-deep);color:var(--white)}
.footer-col{position:absolute;top:56px}
.footer-col h5{font-family:"Crimson Pro",serif;font-size:19px;margin-bottom:14px}
.footer-col li{list-style:none;font-size:14px;line-height:26px;color:#dbe6f3}
.footer-col .gap{height:14px}
.footer-col .row{display:flex;align-items:flex-start;gap:12px;font-size:13px;line-height:20px;color:#dbe6f3;margin-bottom:12px}
.footer-col .row svg{flex:none;margin-top:2px}
.social li{display:flex;align-items:center;gap:10px;line-height:36px}
.social i{width:24px;height:24px;border:1.5px solid var(--white);border-radius:50%}
.copyright{position:absolute;left:0;width:1200px;top:2786px;height:53px;background:var(--blue-dark);text-align:center;font-size:12px;line-height:53px;color:#b8cbe2}
</style>
</head>
<body>

<header class="site-header">
  <div class="brand"><span class="brand-dot"></span><span class="brand-name">Briar Hollow Gathering Church</span></div>
  <div class="header-contact">
    <small>Contact Us Now</small>
    <strong><svg width="22" height="22" viewBox="0 0 24 24"><path fill="#0792cd" d="M6.6 10.8a15 15 0 0 0 6.6 6.6l2.2-2.2a1 1 0 0 1 1-.25 11.4 11.4 0 0 0 3.6.6 1 1 0 0 1 1 1V20a1 1 0 0 1-1 1A17 17 0 0 1 3 4a1 1 0 0 1 1-1h3.5a1 1 0 0 1 1 1c0 1.25.2 2.450.6 3.6a1 1 0 0 1-.25 1z"/></svg>555.014.2270</strong>
  </div>
</header>

<nav class="main-nav">
  <ul>
    <li class="active">HOME</li><li>AGE GROUP</li><li>ACTIVITIES</li><li>EVENTS CALENDAR</li><li>ABOUT</li><li>CONTACT</li>
  </ul>
</nav>

<section class="hero">
  <div class="hero-photo" role="img" aria-label="Lit candles glowing around a brass candle stand in a dim church"></div>
  <h2 class="hero-title">BLESSINGS FROM BRIAR HOLLOW<br>GATHERING CHURCH!</h2>
  <div class="hero-dots"><span class="on"></span><span></span><span></span><span></span></div>
  <div class="email-form">
    <h2>FORM TO<br>EMAIL CHURCH</h2>
    <p>Proin nulla arcu nonummy luctus dictum</p>
    <div class="field">Name</div>
    <div class="field">Email address</div>
    <div class="submit">SUBMIT NOW</div>
  </div>
</section>

<section class="welcome">
  <div class="kicker"><i></i>WELCOME TO<i></i></div>
  <h1>BRIAR HOLLOW GATHERING CHURCH</h1>
  <p>We hold two services which are at 8 am (traditional worship service where we sing hymns) and at 10 am (family worship service) where the children would head off to join the Micro Minis, Sunday Club or (Junior) Juice during the sermon. Holy Communion is generally held on the 3rd Sunday of the month. Our Minister is the Reverend Alan Marsh.</p>
  <span class="btn-orange">ASK A QUESTION</span>
</section>

<section class="activities">
  <h2 class="section-title">ACTIVITY AREAS</h2>
  <div class="activity-cards">
    <div class="activity-card"><div class="photo" role="img" aria-label="Parents and toddlers at a playgroup session" style="background:linear-gradient(135deg,#a07d5c,#6b4a36)"></div><div class="label">Koala Kids Playgroup</div></div>
    <div class="activity-card"><div class="photo" role="img" aria-label="Youth group member in the church hall" style="background:linear-gradient(135deg,#b9b4a8,#5f7a70)"></div><div class="label">Youth Groups</div></div>
    <div class="activity-card"><div class="photo" role="img" aria-label="Children gathered together in a prayer group" style="background:linear-gradient(135deg,#8e3b3b,#4a3a40)"></div><div class="label">Prayer Group</div></div>
    <div class="activity-card"><div class="photo" role="img" aria-label="Men chatting over coffee in the hall" style="background:linear-gradient(135deg,#9a8f84,#3e3a3a)"></div><div class="label">Mens Coffee Group</div></div>
  </div>
</section>

<section class="minister">
  <h2>MINISTER'S WEEKLY MESSAGE</h2>
  <p>interdum vel blandit sed nulla In ullamcorper est eget tempor cursus neque mi consectetuer mi a ultricies massa est sed nisl Class aptent taciti sociosqu ad litora torquent per conubia nostra per inceptos hymenaeos Proin nulla arcu nonummy luctus dictum eget</p>
  <span class="btn-outline">READ MORE</span>
</section>

<section class="panels">
  <div class="panel prayer" role="img" aria-label="Open bible on a dark table, behind a prayer request form">
    <h3>PRAYER REQUEST</h3>
    <div class="sub">ENTER YOUR REQUEST HERE</div>
    <p>or cursus neque mi consectetuer mi a ultricies massa est sed nisl Class aptent taciti sociosqu ad litora</p>
    <div class="prayer-form"><div class="field">Email address</div><div class="submit">SUBMIT</div></div>
  </div>
  <div class="panel mission" role="img" aria-label="Church interior with pews, tinted orange">
    <h3>THEME/MISSION</h3>
    <p>ut tincidunt sed diam Donec quis mi sed magna hendrerit accumsan Suspendisse risus nibh ultricies eu volutpat non condimentum</p>
    <span class="btn-outline">READ MORE</span>
  </div>
</section>

<section class="news">
  <h2 class="section-title">NEWS</h2>
  <div class="news-list">
    <div class="news-item"><div class="photo" role="img" aria-label="Members smiling at a church gathering" style="background:linear-gradient(135deg,#b86b5a,#4a3a36)"></div><h4>At tincidunt sed diam</h4><p>Donec quis mi sed magna hendrerit accumsan Suspendisse risus nibh ultricies eu volutpat non condimentum hendrerit augue</p><a>READ MORE</a></div>
    <div class="news-item"><div class="photo" role="img" aria-label="Ladies sharing a meal at a long table" style="background:linear-gradient(135deg,#b48a96,#5a4a50)"></div><h4>Donec scelerisque leo</h4><p>Donec quis mi sed magna hendrerit accumsan Suspendisse risus nibh ultricies eu volutpat non condimentum hendrerit augue</p><a>READ MORE</a></div>
    <div class="news-item"><div class="photo" role="img" aria-label="Volunteer preparing food in the church kitchen" style="background:linear-gradient(135deg,#8a7a6a,#3d4a5a)"></div><h4>Pellentesque faucibus</h4><p>Donec quis mi sed magna hendrerit accumsan Suspendisse risus nibh ultricies eu volutpat non condimentum hendrerit augue</p><a>READ MORE</a></div>
  </div>
</section>

<footer class="site-footer">
  <div class="footer-col" style="left:127px">
    <h5>INFORMATION</h5>
    <ul><li>Home</li><li>Age Group</li><li>Activities</li><li>Events Calendar</li><li>About</li><li>Contact</li></ul>
  </div>
  <div class="footer-col" style="left:363px">
    <h5>SERVICE TIMES</h5>
    <ul><li>Monday to Friday</li><li>10 am to 08 Pm</li><li class="gap"></li><li>Saturday &amp; Sunday</li><li>11 am to 06 Pm</li></ul>
  </div>
  <div class="footer-col" style="left:644px">
    <h5>CONTACT US</h5>
    <div class="row"><svg width="14" height="18" viewBox="0 0 14 18"><path fill="none" stroke="#fff" stroke-width="1.5" d="M7 17s6-6.5 6-10.5A6 6 0 0 0 1 6.5C1 10.5 7 17 7 17z"/><circle cx="7" cy="6.5" r="2" fill="none" stroke="#fff" stroke-width="1.5"/></svg><span>18 Elm Lane Suite 4 Briar Hollow,<br>ST 00000 Voice 555.014.3381</span></div>
    <div class="row"><svg width="16" height="16" viewBox="0 0 24 24"><path fill="none" stroke="#fff" stroke-width="2" d="M6.6 10.8a15 15 0 0 0 6.6 6.6l2.2-2.2a1 1 0 0 1 1-.25 11.4 11.4 0 0 0 3.6.6 1 1 0 0 1 1 1V20a1 1 0 0 1-1 1A17 17 0 0 1 3 4a1 1 0 0 1 1-1h3.5a1 1 0 0 1 1 1c0 1.25.2 2.45.6 3.6a1 1 0 0 1-.25 1z"/></svg><span>Phone:+1 555-014-7720</span></div>
    <div class="row"><svg width="18" height="14" viewBox="0 0 18 14"><rect x="1" y="1" width="16" height="12" fill="none" stroke="#fff" stroke-width="1.5"/><path d="M1 1l8 7 8-7" fill="none" stroke="#fff" stroke-width="1.5"/></svg><span>hello@briarhollow.example</span></div>
  </div>
  <div class="footer-col social" style="left:967px">
    <h5>FOLLOW US</h5>
    <ul><li><i></i>Friendpage</li><li><i></i>Chirpline</li><li><i></i>Circleplus</li><li><i></i>Viewtube</li></ul>
  </div>
</footer>
<div class="copyright">© 2016 Company Name &nbsp;All right reserved &nbsp;Term of Use</div>

</body>
</html>
```